Small legal and financial translation company needs Squarespace website, brochure and logo

Hello,
We are Lumarin Services (www.lumarinservices-example.com), a boutique legal and financial translation company. We offer our services mainly to Spanish customers. Our primary line of business is the translation of financial statements, but we translate a wide variety legal and financial texts.
The project we are offering comprises three parts: a redo of the current website, an informational brochure for potential customer and a logo design. These three parts should provide a consistent image. We would develop content soon.
We are looking for a website that would look like a typical law firm website, nothing too fancy. Right now, it is in English, Spanish and French, although the new site need only be in English and Spanish. There must be good toggling between the English and Spanish versions. There would be no need for tie-ins to social media and it would not contain a blog. Basically, a static site. We aren't interesting in driving traffic to the site or SEO, as we will contact nearly all potential customers beforehand. The website must be built in Squarespace to enable a smooth transition. The content would be similar to the current page, we'll be working on the exact content, but a rough draft is attached.
The brochure will be some three pages and would introduce the company to potential customers, using similar images as the website and the logo to be designed.
The only specifications for the logo is, as the website and brochure, it convey a sense of security and trust.
Feel free to ask with any questions as this is the first time we have used this platform.
Thank you!
Updates

I've added a more or less final version for the text in the brochure and updated the brief. Added Wednesday, June 10, 2015

Target Market(s)

Spanish law firms, auditors, accountants, banks, investment firms

Industry/Entity Type

Finance

Logo Text

Lumarin Services

Number of Pages Required

5+ page

Font styles to use
Serif

Requirements
Must have
• The website must be built in Squarespace and have a good option to toggle between English and Spanish versions.
• Brochure must be in both English and Spanish, I'm attaching a rough draft of the information that it will probably have. This should give an idea about what to include and the spacing. I will update it to include the final information.
Nice to have
• Would be nice to have some quality finance- and legal-related images
Should not have
• Vibrant colours

```html
<!DOCTYPE html>
<html lang="en">
<head>
<meta charset="utf-8">
<title>Lumarin Services — Legal &amp; Financial Translation</title>
<link href="https://fonts.googleapis.com/css2?family=Cinzel:wght@400;700&family=Crimson+Text:wght@400;600&family=Open+Sans:wght@300;400;600&display=swap" rel="stylesheet">
<style>
:root{
  --brand-blue:#2b4a8e;
  --heading-blue:#2d4b8f;
  --black:#000;
  --white:#fff;
  --text:#222;
  --muted:#bdbdbd;
  --band-grey:#e6e6e6;
  --dark-1:#1b1b1b;
  --dark-2:#3a3a3a;
  --line:#d4d4d4;
  --link:#3d8bd6;
  --client-grey:#444;
}
*{margin:0;padding:0;box-sizing:border-box}
html,body{width:1200px;height:2289px;overflow:hidden;background:var(--white)}
body{position:relative;font-family:'Open Sans',Arial,sans-serif;color:var(--text)}
.abs{position:absolute}

/* top bar */
.top-bar{left:0;top:0;width:1200px;height:29px;background:var(--black);color:var(--white);font-size:11px}
.lang-select{right:82px;top:6px;display:flex;align-items:center;gap:6px}
.lang-box{border:1px solid #aaa;padding:0 6px;height:17px;line-height:15px;font-size:11px;display:flex;gap:6px;align-items:center}

/* header */
.site-header{left:0;top:29px;width:1200px;height:97px;background:var(--white)}
.brand{left:101px;top:35px;display:flex;align-items:center;gap:10px}
.brand-square{width:46px;height:46px;background:var(--brand-blue)}
.brand-name{font-family:'Crimson Text',Georgia,serif;font-size:34px;color:var(--black);letter-spacing:1px;text-transform:uppercase}
.main-nav{top:42px;font-family:'Crimson Text',Georgia,serif;font-size:19px;color:var(--black)}

/* hero */
.hero{left:0;top:126px;width:1200px;height:452px;background:linear-gradient(180deg,#8c8c8c 0%,#bdbdbd 30%,#9a9a9a 70%,#5c5c5c 100%)}
.hero-band{left:0;top:578px;width:1200px;height:248px;background:var(--band-grey)}
.hero-title{left:0;top:280px;width:687px;height:83px;background:rgba(255,255,255,.78);display:flex;align-items:center;padding-left:104px;font-size:31px;font-weight:400;letter-spacing:-.3px;white-space:nowrap;color:var(--heading-blue)}

.service-card{top:546px;width:467px;height:229px;background:var(--black);color:var(--white);text-align:center;box-shadow:0 26px 22px -14px rgba(0,0,0,.35)}
.service-card h3{font-family:'Cinzel',serif;font-weight:400;font-size:20px;letter-spacing:1px;margin-top:80px}
.service-card p{font-size:14.5px;line-height:18px;margin:6px auto 0;width:400px}
.btn{display:inline-block;border:1.5px solid currentColor;border-radius:5px;font-size:14px;width:96px;height:30px;line-height:27px;text-align:center}
.service-card .btn{margin-top:14px;color:var(--white)}
.service-icon{top:-57px;left:176px;width:115px;height:115px;border-radius:50%;background:var(--brand-blue);border:4px solid var(--white);display:flex;align-items:center;justify-content:center}

/* about */
.section-heading{font-family:'Cinzel',serif;font-weight:400;color:var(--heading-blue);font-size:28px;letter-spacing:1px}
.about-col{top:896px;width:452px}
.about-col p{font-size:14px;line-height:22.6px;text-align:justify;margin-top:14px;color:#111}
.about-col .btn{position:absolute;top:247px;color:var(--black)}

/* why choose */
.why{left:0;top:1240px;width:1200px;height:449px;background:linear-gradient(120deg,var(--dark-1) 0%,#111 40%,var(--dark-2) 75%,#1f1f1f 100%)}
.why-heading{left:0;top:1284px;width:1200px;text-align:center;color:var(--white)}
.feature{width:350px;height:150px;color:var(--white)}
.feature-icon{left:0;top:0;width:62px;height:62px;border:2px solid var(--white);border-radius:50%;display:flex;align-items:center;justify-content:center}
.feature h4{position:absolute;left:77px;top:8px;font-family:'Crimson Text',Georgia,serif;font-weight:400;font-size:19px}
.feature p{position:absolute;left:77px;top:38px;width:220px;font-size:12px;line-height:17px;color:var(--muted)}
.grid-line{background:rgba(255,255,255,.12)}

/* clients */
.clients-heading{left:0;top:1768px;width:1200px;text-align:center}
.client-row{left:101px;top:1847px;width:998px;height:103px;display:flex;border:1px solid var(--line)}
.client{flex:1;border-right:1px solid var(--line);display:flex;align-items:center;justify-content:center;gap:8px}
.client:last-child{border-right:none}
.client-dot{width:14px;height:14px;border-radius:50%;background:var(--client-grey)}
.client-name{font-family:'Crimson Text',Georgia,serif;font-size:19px;font-weight:400;color:var(--client-grey)}

/* footer */
.site-footer{left:0;top:2003px;width:1200px;height:286px;background:var(--black);color:var(--white)}
.footer-col{top:42px}
.footer-col h5{font-size:15.5px;font-weight:600;margin-bottom:17px}
.footer-col h5.serv{font-weight:400}
.footer-col ul{list-style:none}
.footer-col li{font-size:13.5px;line-height:31.5px;padding-left:16px;position:relative}
.footer-col li::before{content:"";position:absolute;left:2px;top:14px;width:4px;height:4px;border-radius:50%;background:var(--white)}
.contact-info{width:225px}
.contact-info p{font-size:13.5px;line-height:21px;margin-bottom:11px}
.contact-info a{color:var(--link);text-decoration:none;font-size:12.5px}
.map{left:851px;top:78px;width:250px;height:138px;background:linear-gradient(135deg,#d9d6cc,#e8e4da 50%,#cfcabe)}
</style>
</head>
<body>

<div class="abs top-bar">
  <div class="abs lang-select">Select Language: <span class="lang-box">English <svg width="7" height="5" viewBox="0 0 7 5"><path d="M0 0h7L3.5 5z" fill="#fff"/></svg></span></div>
</div>

<header class="abs site-header">
  <div class="abs brand"><span class="brand-square"></span><span class="brand-name">Lumarin Services</span></div>
  <nav>
    <span class="abs main-nav" style="left:632px">Home</span>
    <span class="abs main-nav" style="left:717px">About Us</span>
    <span class="abs main-nav" style="left:828px">Services</span>
    <span class="abs main-nav" style="left:930px">FAQ's</span>
    <span class="abs main-nav" style="left:1016px">Contact Us</span>
  </nav>
</header>

<section class="abs hero" role="img" aria-label="Black and white photo of a person signing a document beside a statue of Lady Justice holding scales"></section>
<div class="abs hero-band"></div>
<h1 class="abs hero-title">HIGH-QUALITY TRANSLATION SERVICES</h1>

<article class="abs service-card" style="left:113px">
  <div class="abs service-icon">
    <svg width="56" height="56" viewBox="0 0 56 56" fill="#fff"><rect x="14" y="8" width="26" height="12" rx="2" transform="rotate(35 27 14)"/><rect x="24" y="20" width="6" height="28" transform="rotate(-55 27 34)"/><rect x="8" y="44" width="24" height="5" rx="1"/></svg>
  </div>
  <h3>Legal Translation</h3>
  <p>Lorem ipsum dolor sit amet, consectetuer adipiscing elit, sed diam nonummy nibh euismod tincidunt ut.</p>
  <span class="btn">More</span>
</article>

<article class="abs service-card" style="left:618px">
  <div class="abs service-icon">
    <svg width="56" height="56" viewBox="0 0 56 56" fill="none" stroke="#fff" stroke-width="3"><rect x="9" y="9" width="38" height="36" rx="3"/><circle cx="28" cy="27" r="8"/><path d="M14 48v3M42 48v3M28 19v-3M28 35v3"/></svg>
  </div>
  <h3>Financial Translation</h3>
  <p>Lorem ipsum dolor sit amet, consectetuer adipiscing elit, sed diam nonummy nibh euismod tincidunt ut.</p>
  <span class="btn">More</span>
</article>

<section class="abs about-col" style="left:114px">
  <h2 class="section-heading">Who Are We?</h2>
  <p>We are a small, highly professional and qualified group of professionals with backgrounds in law, financial services and translation and interpretation that boasts experience in global consulting and auditing firms, law firms and companies from a cross section of industries. Sensitive to the workings of the financial world, we are detail-oriented experts striving to facilitate understanding among investors, companies and international organisations.</p>
  <span class="btn" style="left:4px">More</span>
</section>

<section class="abs about-col" style="left:626px">
  <h2 class="section-heading">What We Do?</h2>
  <p>We provide high-quality translation services in English, Spanish and French for legal and financial documents, particularly for your company's financial statements and annual reports. The translation tools we have fashioned over the years ensure that your investors and other parties recognise your company's worth and dedication while reflecting the distinction between financial statements prepared under IFRSs or local GAAP.</p>
  <span class="btn" style="left:4px">More</span>
</section>

<section class="abs why" role="img" aria-label="Dark black and white photo of modern glass office towers"></section>
<h2 class="abs section-heading why-heading">Why Choose Us?</h2>
<div class="abs grid-line" style="left:410px;top:1340px;width:1px;height:310px"></div>
<div class="abs grid-line" style="left:763px;top:1340px;width:1px;height:310px"></div>
<div class="abs grid-line" style="left:76px;top:1498px;width:1050px;height:1px"></div>

<div class="abs feature" style="left:99px;top:1356px">
  <div class="abs feature-icon"><svg width="30" height="30" viewBox="0 0 30 30" fill="#fff"><ellipse cx="15" cy="16" rx="11" ry="8"/><rect x="8" y="21" width="3" height="6"/><rect x="19" y="21" width="3" height="6"/></svg></div>
  <h4>Save Money</h4>
  <p>Lorem ipsum dolor sit amet, consectetuer adipiscing elit, sed diam nonummy nibh euismod.</p>
</div>
<div class="abs feature" style="left:442px;top:1356px">
  <div class="abs feature-icon"><svg width="30" height="30" viewBox="0 0 30 30" fill="#fff"><path d="M15 3l3.5 7.5 8 1-6 5.5 1.6 8L15 21l-7.1 4 1.6-8-6-5.5 8-1z"/></svg></div>
  <h4>Quality Guaranteed</h4>
  <p>Lorem ipsum dolor sit amet, consectetuer adipiscing elit, sed diam nonummy nibh euismod.</p>
</div>
<div class="abs feature" style="left:785px;top:1356px">
  <div class="abs feature-icon"><svg width="30" height="30" viewBox="0 0 30 30" fill="#fff"><circle cx="12" cy="11" r="5"/><path d="M3 27c0-6 4-9 9-9s9 3 9 9z"/><circle cx="23" cy="7" r="4" fill="none" stroke="#fff" stroke-width="2"/></svg></div>
  <h4>Native Translators Only</h4>
  <p>Lorem ipsum dolor sit amet, consectetuer adipiscing elit, sed diam nonummy nibh euismod.</p>
</div>
<div class="abs feature" style="left:99px;top:1524px">
  <div class="abs feature-icon"><svg width="30" height="30" viewBox="0 0 30 30" fill="none" stroke="#fff" stroke-width="2.5"><circle cx="15" cy="15" r="11"/><path d="M15 8v7l5 3"/></svg></div>
  <h4>Consistency Over Time</h4>
  <p>Lorem ipsum dolor sit amet, consectetuer adipiscing elit, sed diam nonummy nibh euismod.</p>
</div>
<div class="abs feature" style="left:442px;top:1524px">
  <div class="abs feature-icon"><svg width="30" height="30" viewBox="0 0 30 30" fill="none" stroke="#fff" stroke-width="2.5"><rect x="5" y="6" width="20" height="14" rx="1"/><path d="M2 24h26"/></svg></div>
  <h4>Use of Technology</h4>
  <p>Lorem ipsum dolor sit amet, consectetuer adipiscing elit, sed diam nonummy nibh euismod.</p>
</div>
<div class="abs feature" style="left:785px;top:1524px">
  <div class="abs feature-icon"><svg width="30" height="30" viewBox="0 0 30 30" fill="#fff"><circle cx="15" cy="10" r="4"/><circle cx="7" cy="13" r="3"/><circle cx="23" cy="13" r="3"/><path d="M8 25c0-5 3-8 7-8s7 3 7 8z"/><path d="M1 24c0-4 2-6 6-6 1 0 2 0 2 1-1 1-2 3-2 5z"/><path d="M29 24c0-4-2-6-6-6-1 0-2 0-2 1 1 1 2 3 2 5z"/></svg></div>
  <h4>Years of Experience</h4>
  <p>Lorem ipsum dolor sit amet, consectetuer adipiscing elit, sed diam nonummy nibh euismod.</p>
</div>

<h2 class="abs section-heading clients-heading">Our Clients</h2>
<div class="abs client-row">
  <div class="client"><span class="client-dot"></span><span class="client-name">Client One</span></div>
  <div class="client"><span class="client-dot"></span><span class="client-name">Client Two</span></div>
  <div class="client"><span class="client-dot"></span><span class="client-name">Client Three</span></div>
  <div class="client"><span class="client-dot"></span><span class="client-name">Client Four</span></div>
  <div class="client"><span class="client-dot"></span><span class="client-name">Client Five</span></div>
</div>

<footer class="abs site-footer">
  <div class="abs footer-col" style="left:101px">
    <h5>Quick Links</h5>
    <ul><li>Home</li><li>About Us</li><li>FAQ's</li><li>Our Clients</li><li>Privacy Policy</li></ul>
  </div>
  <div class="abs footer-col" style="left:351px">
    <h5 class="serv">Services We Offer</h5>
    <ul><li>Legal Translation</li><li>Financial Translation</li><li>Document Translation</li><li>Interpreting</li><li>Service Levels</li></ul>
  </div>
  <div class="abs footer-col contact-info" style="left:601px">
    <h5>Contact Info</h5>
    <p>Address: 1180 Harbor Lane<br>Westbrook, ST 40512</p>
    <p>Phone: (555) 014-2290</p>
    <p>Fax: (555) 014-2291</p>
    <p>Mail:<br><a>info@lumarinservices-example.com</a></p>
  </div>
  <div class="abs footer-col" style="left:851px"><h5>Find Us on Map</h5></div>
  <div class="abs map" role="img" aria-label="Street map showing the office location"></div>
</footer>

</body>
</html>
```